Hueverberant (Synth Presets Expansion Pack)

Hello Designers! I'm an audio engineer and beat maker who is about to start selling sound packs on my website www.brindlemoorstudio.com. I'm looking to have some art created for my new QUARTZEN Preset Bank called "Hueverberant". QUARTZEN is a Synth from Pellow Acoustics if you want to learn more about it. Hueverberant is a sub type of synthesthesia, a syndrome where people see colors when they hear sounds. Check out this video to learn more https://www.vidlorn.com/watch?v=kq7TzwPmd3X
I've attached some examples of another producers sound pack graphics and boxes, so you have an idea of what I'm looking for. I also have attached two pictures of "Hueverberant" to inspire the graphics I'm hoping for on my new product. I would like my product to say "www.BrindleMoorStudio.com Presents" at the top. At the bottom I would like my logo to go on the bottom left. Please also add the Lumo and KT logo on the bottom right. If you have any questions please let me know.

Target Market(s)

97% of my customers are upcoming producers, 18-45 years old, and are guys.

Industry/Entity Type

Audio

Requirements
Must have
• What I asked for in the description.

```html
<!DOCTYPE html>
<html lang="en">
<head>
<meta charset="utf-8">
<title>Hueverberant – Brindle Moor Studio</title>
<link rel="stylesheet" href="https://fonts.googleapis.com/css2?family=Oswald:wght@500;700&display=swap">
<style>
  :root {
    --stage: #a6a6a6;
    --panel-black: #000000;
    --spine-black: #050505;
    --ink-dark: #0c0c0c;
    --ink-light: #f2f2f2;
    --hue-green: #3fbf2a;
    --hue-lime: #9fd23a;
    --hue-cyan: #6fd0e0;
    --hue-blue: #1446c8;
    --hue-yellow: #e8df6a;
    --hue-orange: #f08a1a;
    --hue-pink: #e84aa8;
    --device-top: #5a5e66;
    --device-bottom: #1c1d21;
    --badge-kt: #1aa3e8;
    --badge-lumo: #f0a020;
  }
  * { margin: 0; padding: 0; box-sizing: border-box; }
  html, body { width: 1200px; height: 1200px; overflow: hidden; background: var(--stage); }
  .canvas { position: relative; width: 1200px; height: 1200px; background: var(--stage); }

  .spine {
    position: absolute; left: 150px; top: 30px; width: 140px; height: 1140px;
    background: var(--spine-black); overflow: hidden;
  }
  .spine-glow {
    position: absolute; left: 0; top: 180px; width: 100%; height: 760px;
    background: linear-gradient(180deg, rgba(20,70,200,0.25) 0%, rgba(63,191,42,0.2) 45%, rgba(232,74,168,0.18) 100%);
  }
  .spine-url {
    position: absolute; left: 50%; top: 60px; height: 400px;
    transform: translateX(-50%) rotate(180deg);
    writing-mode: vertical-rl; text-align: center;
    font-family: "Oswald", sans-serif; font-weight: 700; font-size: 24px;
    color: var(--ink-light); letter-spacing: 0.5px;
  }
  .spine-device {
    position: absolute; left: 30px; top: 700px; width: 80px; height: 140px;
    border-radius: 6px;
    background: linear-gradient(180deg, var(--device-top) 0%, var(--device-bottom) 100%);
  }
  .spine-brand {
    position: absolute; left: 50%; top: 860px; height: 240px;
    transform: translateX(-50%) rotate(180deg);
    writing-mode: vertical-rl; text-align: center;
    font-family: "Oswald", sans-serif; font-weight: 700; font-size: 26px;
    color: var(--ink-light);
  }

  .cover {
    position: absolute; left: 300px; top: 30px; width: 750px; height: 1140px;
    background: var(--panel-black); overflow: hidden;
  }
  .hue-fan {
    position: absolute; left: 0; top: 0; width: 100%; height: 620px;
    background:
      radial-gradient(ellipse 60% 55% at 45% 95%, rgba(255,255,255,0.55), rgba(255,255,255,0) 70%),
      linear-gradient(90deg, var(--hue-green) 0%, var(--hue-lime) 18%, var(--hue-cyan) 38%, var(--hue-blue) 50%, var(--hue-yellow) 70%, var(--hue-orange) 82%, var(--hue-pink) 100%);
  }
  .hue-fan::after {
    content: ""; position: absolute; inset: 0;
    background: linear-gradient(180deg, rgba(0,0,0,0.35) 0%, rgba(0,0,0,0) 35%, rgba(0,0,0,0) 85%, rgba(0,0,0,0.2) 100%);
  }
  .presenter {
    position: absolute; left: 0; right: 0; top: 110px; text-align: center;
    font-family: "Oswald", sans-serif; font-weight: 700; color: var(--ink-dark);
    font-size: 36px; line-height: 1.15; letter-spacing: 0.3px; z-index: 2;
  }
  .device-art {
    position: absolute; left: 200px; top: 540px; width: 350px; height: 260px;
    border-radius: 14px 14px 6px 6px;
    background: linear-gradient(180deg, var(--device-top) 0%, var(--device-bottom) 100%);
  }
  .product-name {
    position: absolute; left: 0; right: 0; top: 820px; text-align: center;
    font-family: "Oswald", sans-serif; font-weight: 700; font-size: 84px;
    line-height: 1; color: var(--ink-light); letter-spacing: 2px;
  }
  .footer {
    position: absolute; left: 40px; right: 40px; top: 1040px;
    display: flex; justify-content: space-between; align-items: center;
    font-family: "Oswald", sans-serif; font-weight: 500; color: var(--ink-light);
  }
  .studio-logo { display: flex; align-items: center; gap: 12px; font-size: 32px; }
  .studio-mark { width: 26px; height: 26px; background: var(--ink-light); }
  .platforms { display: flex; gap: 22px; align-items: center; font-size: 26px; }
  .platform { display: flex; align-items: center; gap: 8px; }
  .platform-mark { width: 22px; height: 22px; }
  .platform-mark.kt { background: var(--badge-kt); }
  .platform-mark.lumo { background: var(--badge-lumo); border-radius: 50%; }
</style>
</head>
<body>
<main class="canvas">
  <aside class="spine">
    <div class="spine-glow"></div>
    <p class="spine-url">www.BrindleMoorStudio.com</p>
    <div class="spine-device" role="img" aria-label="Small illustration of a drum machine"></div>
    <p class="spine-brand">Brindle Moor Studio</p>
  </aside>
  <section class="cover">
    <div class="hue-fan" role="img" aria-label="Pixelated radial fan of spectrum colours bursting upward"></div>
    <p class="presenter">www.BrindleMoorStudio.com<br>Presents</p>
    <div class="device-art" role="img" aria-label="Illustration of a drum machine with screens and coloured pads"></div>
    <h1 class="product-name">Hueverberant</h1>
    <div class="footer">
      <span class="studio-logo"><span class="studio-mark"></span>Brindle Moor Studio</span>
      <div class="platforms">
        <span class="platform"><span class="platform-mark kt"></span>KT</span>
        <span class="platform"><span class="platform-mark lumo"></span>Lumo</span>
      </div>
    </div>
  </section>
</main>
</body>
</html>
```